Lorvex Tilo medical cannibis cultivation company

tag - Tilo rise
Lorvex Tilo medical cannabis cultivation - logo is selected- can we please see bold examples with our selection. We are mainly dealing with medical companies and professionals. We would like to be stand out in the crowd with our designs. Welcome any and all attempts. Thanks

Target Market(s)

Medical and Professional

Industry/Entity Type

Medical And Science

Font styles to use
Sans Serif

Colors

Designer to choose colors to be used in the design.

Requirements
Must have
• Bright colour and be bold- Love the teal and magenta that is currently on the dark background design.
Nice to have
• shading and the 3D affect- The shadowed appearance.
Should not have
• Anything related to illegal activity or un professional manners

```html
<!DOCTYPE html>
<html lang="en">
<head>
<meta charset="utf-8">
<title>Lorvex Tilo – Business Card</title>
<link rel="stylesheet" href="https://fonts.googleapis.com/css2?family=Roboto:wght@400;500;700&display=swap">
<style>
  :root {
    --stage: #e9e6e2;
    --card-black: #000000;
    --teal: #00ade6;
    --magenta: #9c4a98;
    --white: #ffffff;
    --grey: #8d9196;
    --ink-line: #111111;
  }
  * { margin: 0; padding: 0; box-sizing: border-box; }
  html, body {
    width: 1125px; height: 1200px; overflow: hidden;
    background: var(--stage);
    font-family: 'Roboto', Arial, sans-serif;
  }
  .stage { position: relative; width: 1125px; height: 1200px; }
  .card {
    position: absolute; left: 150px;
    width: 800px; height: 456px;
    border-radius: 22px; overflow: hidden;
    transform: scale(1.0325); transform-origin: 0 0;
    box-shadow: 0 4px 10px rgba(0,0,0,.25);
  }
  .card--front { top: 98px; background: var(--card-black); }
  .card--back { top: 632px; background: var(--magenta); }
  .front-art { position: absolute; inset: 0; width: 800px; height: 456px; }

  .brand-mark {
    position: absolute; left: 111px; top: 47px;
    width: 146px; height: 146px; border-radius: 50%;
    border: 6px solid var(--grey);
  }
  .brand-name {
    position: absolute; left: 40px; top: 190px; width: 300px;
    text-align: center; color: var(--teal);
    font-size: 37px; font-weight: 700; letter-spacing: 1px;
  }
  .brand-tag {
    position: absolute; left: 58px; top: 236px; width: 250px;
    display: flex; align-items: center; gap: 8px;
    color: var(--grey); font-size: 16px; letter-spacing: 2px;
  }
  .brand-tag::before, .brand-tag::after {
    content: ""; flex: 1; height: 2px; background: var(--grey);
  }

  .contact {
    position: absolute; right: 43px; top: 220px;
    text-align: right; color: var(--white);
  }
  .contact__name { font-size: 27px; font-weight: 700; line-height: 1.1; }
  .contact__role { font-size: 19px; font-weight: 500; margin-top: 2px; }
  .contact__address { font-size: 18px; line-height: 25px; margin-top: 17px; }
  .contact__lines { list-style: none; margin-top: 12px; font-size: 18px; line-height: 25.5px; }
  .contact__lines li { display: flex; justify-content: flex-end; align-items: center; gap: 9px; }
  .contact__lines svg { width: 17px; height: 17px; fill: var(--white); }

  .back-mark {
    position: absolute; left: 270px; top: 95px;
    width: 260px; height: 260px; border-radius: 50%;
    border: 8px solid var(--white);
  }
  .back-name {
    position: absolute; left: 0; right: 0; top: 205px;
    text-align: center; color: var(--white);
    font-size: 32px; font-weight: 700; letter-spacing: 1px;
  }
  .back-url {
    position: absolute; left: 0; right: 0; top: 390px;
    text-align: center; color: var(--white);
    font-size: 18px; letter-spacing: 4.5px;
  }
</style>
</head>
<body>
<main class="stage">
  <section class="card card--front">
    <svg class="front-art" viewBox="0 0 800 456" aria-hidden="true">
      <path d="M0,345 C70,333 110,378 145,433 C330,290 560,175 800,205 L800,456 L0,456 Z" fill="var(--teal)"/>
      <path d="M0,330 C60,322 112,360 150,418 C360,250 620,150 800,196 L800,205 C560,175 330,290 145,433 C110,378 70,333 0,345 Z" fill="var(--magenta)"/>
      <path d="M0,345 C70,333 110,378 145,433 C330,290 560,175 800,205" fill="none" stroke="var(--ink-line)" stroke-width="3"/>
      <circle cx="148" cy="351" r="16" fill="var(--magenta)"/>
    </svg>

    <div class="brand-mark"></div>
    <div class="brand-name">LORVEX TILO</div>
    <div class="brand-tag">TILO RISE</div>

    <div class="contact">
      <p class="contact__name">MAREK DANEL</p>
      <p class="contact__role">CEO/FOUNDER</p>
      <p class="contact__address">4210 Heron Bend Road<br>Juneau, Alaska 34811</p>
      <ul class="contact__lines">
        <li>689 555 0174
          <svg viewBox="0 0 24 24"><path d="M6.6 10.8a15.1 15.1 0 0 0 6.6 6.6l2.2-2.2a1 1 0 0 1 1-.25 11.4 11.4 0 0 0 3.6.6 1 1 0 0 1 1 1V20a1 1 0 0 1-1 1A17 17 0 0 1 3 4a1 1 0 0 1 1-1h3.5a1 1 0 0 1 1 1c0 1.25.2 2.45.6 3.6a1 1 0 0 1-.25 1z"/></svg>
        </li>
        <li>marek@lorvextilo.com
          <svg viewBox="0 0 24 24"><path d="M2 5h20v14H2z" /><path d="M2 5l10 8 10-8" fill="none" stroke="#00ade6" stroke-width="2"/></svg>
        </li>
        <li>www.lorvextilo.com
          <svg viewBox="0 0 24 24"><circle cx="12" cy="12" r="10"/><path d="M12 2v20M2 12h20M5 6c4 2 10 2 14 0M5 18c4-2 10-2 14 0" fill="none" stroke="#00ade6" stroke-width="1.5"/></svg>
        </li>
      </ul>
    </div>
  </section>

  <section class="card card--back">
    <div class="back-mark"></div>
    <div class="back-name">LORVEX TILO</div>
    <p class="back-url">www.lorvextilorise.com</p>
  </section>
</main>
</body>
</html>
```